Business Card Design - ChoiceCraft

Looking for creative, modern design, two sided for ChoiceCraft that is consistent with color and feel of website www.choicecraftpro.net.
Updates

Back of card will be used to promote products or have a quote revolving around decisions, change, leadership, innovation, creativity. Back should also have space to promote website, but optional to use the icon. Front of the card will need to use the icon and have standard place for name, job title, phone and email. We are not looking to put a mailing address or fax. Also want space to place a few words/phrase explaining what we do...such as individual growth and organizational development or tools, training, information...in addition, want the facebook icon small on the front somewhere as we are also on facebook.

Vector file uploaded of icon.

Target Market(s)

Professional coaching for individual growth and organizational development

Industry/Entity Type

Business

Requirements
Must have
• Icon...see attached.

```html
<!DOCTYPE html>
<html lang="en">
<head>
<meta charset="utf-8">
<title>ChoiceCraft Business Card</title>
<link rel="stylesheet" href="https://fonts.googleapis.com/css2?family=Arimo:wght@400;700&display=swap">
<style>
  :root {
    --page: #e6e7e9;
    --card-white: #ffffff;
    --ink: #1b1b1b;
    --ink-soft: #333333;
    --divider: #c9c9c9;
    --blue-deep: #1a9fdc;
    --blue-mid: #2fb4e9;
    --blue-light: #8fd6f5;
    --band-light: #7fd0f3;
    --logo-ring: #2a8fd6;
    --white: #ffffff;
  }
  * { box-sizing: border-box; margin: 0; padding: 0; }
  html, body {
    width: 1200px; height: 1053px; overflow: hidden;
    background: var(--page);
    font-family: "Arimo", Arial, sans-serif;
  }
  .card {
    position: absolute;
    width: 767px; height: 437px;
    overflow: hidden;
    box-shadow: 0 2px 6px rgba(0,0,0,.18);
  }
  /* Front */
  .card-front { left: 67px; top: 55px; background: var(--card-white); }
  .brand-mark {
    position: absolute; left: 113px; top: 40px;
    width: 170px; height: 170px; border-radius: 50%;
    background: radial-gradient(circle at 45% 40%, #d8e6f2, var(--logo-ring));
  }
  .brand-name {
    position: absolute; left: 68px; top: 282px; width: 290px;
    text-align: center;
    font-weight: 700; font-size: 36px; letter-spacing: .5px;
    color: var(--ink);
  }
  .divider {
    position: absolute; left: 396px; top: 135px;
    width: 3px; height: 193px; background: var(--divider);
  }
  .person {
    position: absolute; left: 424px; top: 155px;
    font-size: 26px; color: var(--ink);
  }
  .person .name { font-weight: 700; }
  .person .title { font-size: 19px; color: var(--ink-soft); }
  .contact-list {
    position: absolute; left: 424px; top: 206px;
    list-style: none; font-size: 20px; color: var(--ink-soft);
  }
  .contact-list li { display: flex; align-items: center; height: 26.5px; }
  .contact-list svg { width: 14px; height: 14px; margin-right: 9px; flex: none; }
  .rule-thin {
    position: absolute; left: 0; top: 380px; width: 100%; height: 3px;
    background: var(--blue-deep);
  }
  .tagline-band {
    position: absolute; left: 0; top: 389px; width: 100%; height: 48px;
    background: linear-gradient(90deg, var(--band-light), var(--blue-mid));
    color: var(--white); font-size: 19px;
    padding: 12px 0 0 60px; letter-spacing: .3px;
  }
  /* Back */
  .card-back {
    left: 365px; top: 552px;
    background: linear-gradient(120deg, var(--blue-mid) 0%, var(--blue-deep) 35%, var(--blue-mid) 65%, var(--blue-light) 100%);
    color: var(--white);
  }
  .quote-list { position: absolute; left: 55px; top: 40px; list-style: none; }
  .quote { height: 76px; font-size: 19px; line-height: 30px; }
  .quote-text { display: block; position: relative; padding-left: 22px; }
  .quote-text::before {
    content: "\201C"; position: absolute; left: 0; top: -4px;
    font-size: 32px; line-height: 32px; font-weight: 700;
  }
  .quote-text::after {
    content: "\201D"; display: inline-block;
    font-size: 32px; line-height: 0; font-weight: 700;
    vertical-align: -14px; margin-left: 3px;
  }
  .quote-author { display: block; padding-left: 22px; font-weight: 700; }
  .back-mark {
    position: absolute; left: 548px; top: 240px;
    width: 150px; height: 150px; border-radius: 50%;
    background: radial-gradient(circle at 45% 40%, #d8e6f2, var(--logo-ring));
  }
</style>
</head>
<body>
  <section class="card card-front">
    <div class="brand-mark"></div>
    <div class="brand-name">ChoiceCraft</div>
    <div class="divider"></div>
    <div class="person"><span class="name">Your Name,</span> <span class="title">Title</span></div>
    <ul class="contact-list">
      <li><svg viewBox="0 0 14 14"><circle cx="7" cy="7" r="6" fill="none" stroke="#333" stroke-width="1.3"/><path d="M4.5 4 l1.5 0 l.6 1.8 l-.9.7 q.8 1.6 2.1 2.1 l.7-.9 l1.8.6 l0 1.5 q-4.6 .3 -5.8 -5.8z" fill="#333"/></svg>123-456-789</li>
      <li><svg viewBox="0 0 14 14"><rect x="1" y="3" width="12" height="9" fill="#333"/><path d="M1.5 3.5 L7 8 L12.5 3.5" fill="none" stroke="#fff" stroke-width="1.2"/></svg>info@choicecraftpro.net</li>
      <li><svg viewBox="0 0 14 14"><circle cx="7" cy="7" r="6" fill="none" stroke="#333" stroke-width="1.3"/><ellipse cx="7" cy="7" rx="2.5" ry="6" fill="none" stroke="#333"/><path d="M1 7h12" stroke="#333"/></svg>www.choicecraftpro.net</li>
      <li><svg viewBox="0 0 14 14"><rect x="1" y="1" width="12" height="12" fill="#3b5b99"/></svg>/choicecraftpro</li>
    </ul>
    <div class="rule-thin"></div>
    <div class="tagline-band">Supporting individual growth and organizational development.</div>
  </section>

  <section class="card card-back">
    <ul class="quote-list">
      <li class="quote"><span class="quote-text">Try not to become a man of success, but rather a man of value.</span><span class="quote-author">- Arlo Whitfield</span></li>
      <li class="quote"><span class="quote-text">The only constant is change.</span><span class="quote-author">- Corvin Hale</span></li>
      <li class="quote"><span class="quote-text">We are what we repeatedly do. Excellence is not an act, it is a habit.</span><span class="quote-author">- Dorian Vance</span></li>
      <li class="quote"><span class="quote-text">Simplicity is the ultimate sophistication.</span><span class="quote-author">- Lorenzo Bellami</span></li>
      <li class="quote"><span class="quote-text">Life is not fair - get used to it.</span><span class="quote-author">- Wes Tanner</span></li>
    </ul>
    <div class="back-mark"></div>
  </section>
</body>
</html>
```